Restyle corporate identity (+ logo) for a road construction company

We need a new logo and stationary design for our company VARNOK path. VARNOK path® increases the road base strength, while reducing major costs and time of road construction. Attached some examples of the current design.

Our wishes for the new logo:
- Business look
- Style sheet
- Modern

More information: www.varnokpath.example
Updates

Target Market(s)

Government

Industry/Entity Type

Construction

Requirements
Must have
• Logo (with road sign) + text

```html
<!DOCTYPE html>
<html lang="en">
<head>
<meta charset="utf-8">
<title>VARNOK path – Business Card</title>
<link href="https://fonts.googleapis.com/css2?family=PT+Sans:wght@400;700&display=swap" rel="stylesheet">
<style>
  :root {
    --page-bg: #e9e6e1;
    --card-blue-deep: #0b3fd6;
    --card-blue: #1f63f0;
    --card-blue-light: #4f8ff5;
    --text-light: #eef3ff;
    --text-soft: #cfe0ff;
    --panel-frost: rgba(225, 232, 240, 0.82);
    --panel-edge: rgba(255, 255, 255, 0.9);
    --brand-blue: #1546c8;
  }
  * { box-sizing: border-box; margin: 0; padding: 0; }
  html, body {
    width: 1200px; height: 969px; overflow: hidden;
    background: var(--page-bg);
    font-family: "PT Sans", sans-serif;
  }
  .business-card {
    position: absolute;
    left: 100px; top: 200px;
    width: 1000px; height: 568px;
    background: linear-gradient(100deg, var(--card-blue-deep) 0%, var(--card-blue) 45%, var(--card-blue-light) 100%);
    box-shadow: 0 18px 40px rgba(0,0,0,0.25);
    color: var(--text-light);
  }
  .holder-name {
    position: absolute; left: 66px; top: 66px;
    font-size: 33px; font-weight: 400; letter-spacing: 0.5px;
  }
  .holder-role {
    position: absolute; left: 66px; top: 110px;
    font-size: 25px; color: var(--text-soft);
  }
  .postal-address {
    position: absolute; left: 66px; top: 282px;
    font-size: 25px; line-height: 34px; font-style: normal;
    color: var(--text-soft);
  }
  .contact-list {
    position: absolute; left: 66px; top: 410px;
    list-style: none; font-size: 25px; line-height: 40px;
    color: var(--text-soft);
  }
  .contact-list li { display: flex; align-items: center; gap: 14px; }
  .contact-list svg { width: 22px; height: 22px; fill: var(--text-soft); }
  .brand-panel {
    position: absolute; left: 458px; top: 34px;
    width: 515px; height: 509px;
    border-radius: 52px;
    background: var(--panel-frost);
    border: 2px solid var(--panel-edge);
    display: flex; align-items: center; justify-content: center; gap: 16px;
  }
  .brand-mark {
    width: 34px; height: 34px; border-radius: 50%;
    background: var(--brand-blue);
  }
  .brand-name {
    font-size: 58px; font-weight: 700; letter-spacing: 2px;
    color: var(--brand-blue);
  }
</style>
</head>
<body>
  <section class="business-card">
    <h1 class="holder-name">MARA DELVIN</h1>
    <p class="holder-role">CEO/Founder</p>
    <address class="postal-address">
      Havenkade 58<br>
      3011 KT Rotterdam<br>
      The Netherlands
    </address>
    <ul class="contact-list">
      <li>
        <svg viewBox="0 0 24 24" aria-hidden="true"><path d="M6.6 10.8a15.1 15.1 0 0 0 6.6 6.6l2.2-2.2a1 1 0 0 1 1-.25 11.4 11.4 0 0 0 3.6.57 1 1 0 0 1 1 1V20a1 1 0 0 1-1 1A17 17 0 0 1 3 4a1 1 0 0 1 1-1h3.5a1 1 0 0 1 1 1c0 1.25.2 2.45.57 3.6a1 1 0 0 1-.25 1z"/></svg>
        614 208 7351
      </li>
      <li>
        <svg viewBox="0 0 24 24" aria-hidden="true"><path d="M2 5h20v14H2z M4 7v.5l8 5 8-5V7l-8 5z" fill-rule="evenodd"/></svg>
        mara@varnokpath.example
      </li>
      <li>
        <svg viewBox="0 0 24 24" aria-hidden="true"><path d="M12 2a10 10 0 1 0 0 20 10 10 0 0 0 0-20zm6.9 6h-3a15 15 0 0 0-1.3-3.9A8 8 0 0 1 18.9 8zM12 4c.9 1.2 1.6 2.6 2 4h-4c.4-1.4 1.1-2.8 2-4zM4.3 14a8 8 0 0 1 0-4h3.4a16 16 0 0 0 0 4zm.8 2h3a15 15 0 0 0 1.3 3.9A8 8 0 0 1 5.1 16zm3-8h-3a8 8 0 0 1 4.3-3.9A15 15 0 0 0 8.1 8zM12 20c-.9-1.2-1.6-2.6-2-4h4c-.4 1.4-1.1 2.8-2 4zm2.3-6H9.7a14 14 0 0 1 0-4h4.6a14 14 0 0 1 0 4zm.3 5.9a15 15 0 0 0 1.3-3.9h3a8 8 0 0 1-4.3 3.9zm1.7-5.9a16 16 0 0 0 0-4h3.4a8 8 0 0 1 0 4z"/></svg>
        www.varnokpath.example
      </li>
    </ul>
    <div class="brand-panel">
      <span class="brand-mark" aria-hidden="true"></span>
      <span class="brand-name">VARNOK path</span>
    </div>
  </section>
</body>
</html>
```